Poster of Core Values & Motto

Create our core values poster and motto. Attached are our core values and our Motto. This poster represents both of our companies Pindle Shred & KorvaBin.

Target Market(s)

Our team / employees

Industry/Entity Type

Shredding and Medical Waste

Colors
59FF00
82FF00
B8FF75
E3FFCB
F4FFEA
EB3D1F
EC4F4E
F09395
F8D3D4
FCEDEE

Requirements
Must have
• Include both companies logos

```html
<!DOCTYPE html>
<html lang="en">
<head>
<meta charset="utf-8">
<title>Core Values Poster – Pindle Shred &amp; KorvaBin</title>
<link href="https://fonts.googleapis.com/css2?family=Nunito+Sans:wght@700;800;900&display=swap" rel="stylesheet">
<style>
  :root {
    --green: #92c13e;
    --green-pale: #e9f1d6;
    --white: #ffffff;
    --red: #eb3d1f;
  }
  html, body {
    margin: 0;
    padding: 0;
    overflow: hidden;
  }
  .poster {
    position: relative;
    width: 848px;
    height: 1200px;
    background: var(--white);
    overflow: hidden;
    font-family: "Nunito Sans", "Avenir", Arial, sans-serif;
  }
  .motto-word {
    position: absolute;
    margin: 0;
    font-weight: 800;
    color: var(--green);
    line-height: 1;
    white-space: nowrap;
  }
  .motto-purpose { left: 0; top: -15px; font-size: 205px; letter-spacing: 6px; }
  .motto-cause   { left: -4px; top: 272px; font-size: 236px; letter-spacing: -8px; }
  .motto-passion { left: 4px; top: 587px; font-size: 203px; letter-spacing: 17px; }

  .value {
    position: absolute;
    margin: 0;
    color: var(--green-pale);
    line-height: 1;
    white-space: nowrap;
  }
  .value-name { font-weight: 900; font-size: 37px; letter-spacing: 0.5px; text-transform: uppercase; }
  .value-desc { font-weight: 700; font-size: 30px; }
  .align-right { right: 12px; text-align: right; }

  .v-synergy        { top: 171px; }
  .v-synergy-desc   { top: 211px; }
  .v-excellence     { top: 307px; }
  .v-efficient      { top: 429px; }
  .v-efficient-desc { top: 473px; right: 12px; }
  .v-honesty        { top: 543px; left: 64px; }
  .v-safe           { top: 783px; left: 10px; }
  .v-safe-desc      { top: 818px; left: 10px; }
  .v-dependable     { top: 855px; right: 34px; }
  .v-dependable-desc { top: 893px; right: 28px; }

  .service-band {
    position: absolute;
    left: 0;
    top: 940px;
    width: 848px;
    height: 76px;
    background: var(--green);
    color: var(--white);
    display: flex;
    align-items: center;
    justify-content: center;
    font-weight: 900;
    font-size: 26px;
  }
  .brands {
    position: absolute;
    top: 1040px;
    left: 0;
    width: 848px;
    height: 80px;
  }
  .brand {
    position: absolute;
    top: 18px;
    display: flex;
    align-items: center;
    gap: 12px;
    font-weight: 800;
    font-size: 32px;
    line-height: 1;
  }
  .brand-mark {
    width: 40px;
    height: 40px;
    border-radius: 50%;
  }
  .brand-pindle { left: 148px; color: var(--green); }
  .brand-pindle .brand-mark { background: var(--green); }
  .brand-korva { left: 462px; color: var(--red); }
  .brand-korva .brand-mark { background: var(--red); border-radius: 0; }

  .footer-band {
    position: absolute;
    left: 0;
    bottom: 0;
    width: 848px;
    height: 48px;
    background: var(--green);
  }
</style>
</head>
<body>
<main class="poster">
  <h1 class="motto-word motto-purpose">Purpose</h1>
  <p class="value value-name align-right v-synergy">SYNERGY/TEAMWORK</p>
  <p class="value value-desc align-right v-synergy-desc">Get It Done Attitude with Humble confidence</p>

  <p class="value align-right v-excellence"><span class="value-name">EXELLANCE</span> <span class="value-desc">Exceed with a smile</span></p>
  <h1 class="motto-word motto-cause">Cause</h1>
  <p class="value value-name align-right v-efficient">EFFICIENT</p>
  <p class="value value-desc v-efficient-desc">On-Time, sence of urgency, always trying to improve</p>

  <p class="value v-honesty"><span class="value-name">HONESTY/INTEGRITY</span> <span class="value-desc">Do the right thing</span></p>

  <h1 class="motto-word motto-passion">Passion</h1>
  <p class="value value-name v-safe">SAFE AND SECURE</p>
  <p class="value value-desc v-safe-desc">We are just as secure as an armored truck with money</p>
  <p class="value value-name v-dependable">DEPENDABLE</p>
  <p class="value value-desc v-dependable-desc">Do what you say you will do</p>

  <div class="service-band">REMIND PEOPLE WHAT GREAT SERVICE LOOKS LIKE</div>

  <div class="brands">
    <div class="brand brand-pindle"><span class="brand-mark"></span>Pindle Shred</div>
    <div class="brand brand-korva"><span class="brand-mark"></span>KorvaBin</div>
  </div>

  <div class="footer-band"></div>
</main>
</body>
</html>
```